Women's Jewellery startup needs a captivating, beautifully designed and intuitive online store

[12/24 update]

Added 2 additional documents:

Feedback on designs received so far: designer feedback.docx
Product images from catalogue: products images.docx

Please read the feedback provided on designs provided so far to guide you further on your submission. The product images can be used to create promotional banners for the site.

@@@Added a document (VELISTO JEWELLERY_checklist.docx) which can be used by designers as a checklist when submitting their designs to ensure all aspects of the requirements have been covered @@@

+++IMPORTANT BUT NOT SPECIFIED IN THE REQUIREMENTS DOCUMENT - DESIGN SHOULD INCLUDE SUPPORT FOR MOBILE FRIENDLY SITE TOO+++

***Previous experience designing Jewellery online stores preferred (not essential)***

The name of the online Jewellery store is "Velisto Jewellery" and the business is based in Hong Kong. It will be run by 2 stay at home mothers. We need a Shopify themed store designed that will achieve the following objectives in order of priority:

• Conversion: The primary objective of the design/content is to prompt the customer to make a purchase. While this may sound obvious, it is mentioned so as not to distract the design process by focusing on other objectives (which are also important). The site also needs to be optimized so as to rank high in search engine searches for relevant keywords (SEO)
• Navigation: An intuitive interface which takes away a lot of the thinking from the customer by making it obvious what they need to do when they visit the store
• Engagement: Encourages the customer to spend time on the website and share content with their social network

Where applicable, the design of the store should reflect as closely as possible the mission statements and words outlined below:

• Jewellery you’ll fall in love with
• We want every client to leave the store with a smile
• We want to be able to provide the best service we can in every situation no matter what
• We aim to increase our business by word of mouth; therefore we tell people things about our store that makes it interesting for them to share
• We love every customer, no matter how difficult things get
• We, as a team, are so well informed about our products and brands that we always have the best information for our customers
• We celebrate women here!
• We celebrate life in here!
• We celebrate beauty here!
• We celebrate families here, as jewellery often stays within families.
• We will always try to make an extra step
• We will always try to exceed the expectation of our customers
• We will go as far as we possibly can to attract a customer back to our store and connect with us
• Every client that leaves our store knows more about jewellery because we passionately told him about it
• Romantic, classic, love, warm, cool, stylish

A draft functional specification is attached with this brief. We would like the design to reflect as closely as possible the functional requirements outlined in the document. Open to suggestions to improve upon the functional requirements.

Target Market(s)

Women aged 18-55

Industry/Entity Type

Jewelry Store

Coding

Coded - Design and coding required

Number of Pages Required

5+ page

Font styles to use
Other font styles liked:
• Myriad Pro as per Logo but open to any font that complements this one

Requirements
Must have
• 1. A look that encourages the user to make a purchase
• 2. An intuitive, easy to navigate and engaging interface
• 3. Primary colour scheme as defined in the functional specification attached
• 4. Simplistic look, not too cluttered
Nice to have
• 1. Closely matching the functional requirements of the site as outlined in the requirements specification but open to any better ideas

```html
<!DOCTYPE html>
<html lang="en">
<head>
<meta charset="utf-8">
<title>Velisto Jewellery</title>
<link rel="stylesheet" href="https://fonts.googleapis.com/css2?family=Source+Sans+3:wght@400;600;700&family=Playfair+Display:wght@400&display=swap">
<style>
:root{
  --gold:#c9a25a;
  --gold-text:#c29a4e;
  --dark:#333333;
  --darker:#2b2b2b;
  --ink:#222222;
  --muted:#8a8a8a;
  --card:#efefef;
  --line:#dddddd;
  --white:#ffffff;
}
*{margin:0;padding:0;box-sizing:border-box}
html,body{width:811px;height:1200px;overflow:hidden;background:var(--white)}
body{position:relative;font-family:"Source Sans 3",sans-serif;color:var(--ink)}
.abs{position:absolute}
.promo-bar{left:0;top:0;width:811px;height:21px;background:var(--gold);color:var(--white);font-size:9px;text-align:center;line-height:21px}
.util-bar{left:0;top:21px;width:811px;height:24px;background:var(--dark);color:var(--white);font-size:8.5px}
.util-links{position:absolute;right:71px;top:0;height:24px;display:flex;align-items:center;gap:5px}
.cart-count{display:inline-block;width:12px;height:12px;border-radius:50%;background:#111;text-align:center;line-height:12px;font-size:7.5px}
.brand{left:66px;top:52px;width:110px}
.brand-mark{display:flex;align-items:center;gap:5px;margin-left:12px}
.brand-square{width:12px;height:12px;background:var(--gold)}
.brand-name{font-size:16px;letter-spacing:2px;color:var(--gold-text);font-weight:400}
.brand-name small{display:block;font-size:8px;letter-spacing:2.5px}
.brand-tag{font-size:7px;color:#555;margin-top:12px}
.main-nav{top:74px;left:512px;display:flex;gap:20px;font-size:10.5px}
.hero{left:66px;top:121px;width:679px;height:269px;background:#0d0b0a;overflow:hidden}
.hero-photo{position:absolute;left:0;top:0;width:330px;height:269px;background:radial-gradient(ellipse at 40% 45%,#c79a86 0%,#8e5f4e 40%,#2a1a14 75%,#0d0b0a 100%)}
.hero-glow{position:absolute;left:280px;top:0;width:399px;height:269px;background:radial-gradient(ellipse at 70% 40%,#2a2119 0%,#0d0b0a 70%)}
.hero-title{position:absolute;left:329px;top:104px;font-family:"Playfair Display",serif;line-height:1.1}
.hero-title .l1{font-size:36px;color:var(--gold)}
.hero-title .l2{font-size:30px;color:var(--white);display:block}
.dots{left:390px;top:399px;display:flex;gap:8px}
.dots span{width:4px;height:4px;border-radius:50%;background:#444}
.offer{top:414px;width:212px;height:120px;overflow:hidden}
.offer-text{position:absolute;left:90px;top:30px;width:120px;text-align:center}
.offer-text b{display:block;font-size:19px;font-weight:700;color:var(--gold)}
.offer-text p{font-size:8.5px;line-height:1.6;margin-top:2px}
.filters{left:66px;top:545px;width:679px;height:55px;border-top:1px solid var(--line);border-bottom:1px solid var(--line)}
.filter{position:absolute;top:10px;font-size:8.5px;color:#555}
.select{margin-top:5px;height:20px;border:1px solid #ccc;font-size:8.5px;font-weight:600;color:var(--ink);display:flex;align-items:center;justify-content:space-between;padding:0 7px 0 8px}
.select svg{width:7px;height:7px}
.section-title{left:66px;top:609px;font-size:20px;font-weight:400}
.sort-new{left:600px;top:605px;width:109px;margin-top:0}
.pager{left:717px;top:610px;display:flex;gap:4px}
.card{top:642px;width:156px;height:300px;background:var(--card);border:1px solid #e8e8e8}
.card-photo{height:176px;background:var(--white);position:relative}
.card-photo .gem{position:absolute;left:38px;top:22px;width:80px;height:110px;border-radius:40%}
.wish{position:absolute;left:0;right:0;top:124px;text-align:center;font-size:7px}
.wish svg{display:block;margin:4px auto 0;width:12px;height:11px}
.card-body{padding:10px 10px 0}
.card-body h3{font-size:11.5px;font-weight:400}
.card-body .sub{font-size:7.5px;color:var(--muted);margin-top:4px}
.card-body .desc{font-size:7px;line-height:1.5;margin-top:7px;text-align:justify}
.price{font-size:10px;font-weight:700;margin-top:11px}
.actions{display:flex;gap:4px;margin-top:3px}
.btn{height:17px;font-size:7.5px;font-weight:700;color:var(--white);display:flex;align-items:center;justify-content:center}
.btn-cart{width:62px;background:var(--gold)}
.btn-view{width:66px;background:#444}
.footer{left:0;top:957px;width:811px;height:153px;background:var(--dark);color:var(--white)}
.fcol{position:absolute;top:27px}
.fcol h4{font-size:10px;font-weight:700;letter-spacing:.3px}
.fcol ul{list-style:none;margin-top:18px}
.fcol li{font-size:8.5px;height:17.5px;display:flex;align-items:center}
.fcol li::before{content:"›";margin-right:10px;font-size:10px}
.social li::before{content:none}
.social li{height:26.5px}
.social i{width:18px;height:18px;border-radius:50%;margin-right:9px;display:inline-block}
.newsletter-form{position:absolute;left:0;top:29px;display:flex}
.nl-input{width:105px;height:19px;background:var(--white);color:#333;font-size:8px;display:flex;align-items:center;padding-left:8px;gap:8px}
.nl-btn{width:33px;height:19px;background:var(--gold);display:flex;align-items:center;justify-content:center}
.legal{left:0;top:1110px;width:811px;height:90px;background:var(--darker);color:var(--white)}
.pay{position:absolute;left:337px;top:23px;display:flex;gap:6px}
.pay span{width:30px;height:16px;border-radius:2px}
.copy{position:absolute;left:0;width:811px;top:58px;text-align:center;font-size:8.5px}
</style>
</head>
<body>

<div class="abs promo-bar">Free shipping on all orders over $50</div>

<div class="abs util-bar">
  <div class="util-links">
    <span>Sign in</span><span>/</span><span>Wishlist</span><span>/</span><span>HKD</span>
    <svg width="7" height="7" viewBox="0 0 10 10"><path d="M2 3.5l3 3 3-3" stroke="#fff" fill="none" stroke-width="1.3"/></svg>
    <span>/</span><span>My Account</span><span>/</span>
    <svg width="11" height="9" viewBox="0 0 12 10"><path d="M1 1h2l1.5 6h6l1-4.5H4" stroke="#fff" fill="none" stroke-width="1.3"/><circle cx="5" cy="9" r=".9" fill="#fff"/><circle cx="10" cy="9" r=".9" fill="#fff"/></svg>
    <span class="cart-count">0</span><span>/</span>
    <svg width="9" height="9" viewBox="0 0 10 10"><circle cx="4" cy="4" r="3" stroke="#fff" fill="none" stroke-width="1.5"/><path d="M6.3 6.3L9 9" stroke="#fff" stroke-width="1.6"/></svg>
  </div>
</div>

<header>
  <div class="abs brand">
    <div class="brand-mark"><span class="brand-square"></span><span class="brand-name">VELISTO</span></div>
    <div class="brand-tag">Jewellery you'll fall in love with</div>
  </div>
  <nav class="abs main-nav"><span>Home</span><span>Shop</span><span>Blog</span><span>About Us</span><span>Contact</span></nav>
</header>

<section class="abs hero">
  <div class="hero-glow"></div>
  <div class="hero-photo" role="img" aria-label="Woman wearing a diamond drop earring and statement diamond necklace"></div>
  <h1 class="hero-title"><span class="l1">We celebrate</span><span class="l2">women here!</span></h1>
</section>
<div class="abs dots"><span></span><span></span><span></span></div>

<div class="abs offer" style="left:66px;background:linear-gradient(100deg,#e9b9b9 0%,#f6dede 45%,#fbeeee 100%);border:1px solid #eee" role="img" aria-label="Diamond solitaire ring on soft pink fabric">
  <div class="offer-text"><b>Extra 10%</b><p>off Diamond rings till<br>March 31st, 2018</p></div>
</div>
<div class="abs offer" style="left:299px;background:linear-gradient(100deg,#3d2d15 0%,#8a6a2c 35%,#7a5216 70%,#6b4611 100%)" role="img" aria-label="Heap of gold jewellery with gemstones">
  <div class="offer-text" style="color:#fff"><b>Extra 20%</b><p>off Gold sed do eiusmod<br>tempor</p></div>
</div>
<div class="abs offer" style="left:533px;background:linear-gradient(100deg,#2f2f2f 0%,#8f8f8f 30%,#5c5c5c 60%,#4a4a4a 100%)" role="img" aria-label="Silver cuff bracelet and beaded silver jewellery">
  <div class="offer-text" style="color:#fff"><b>Extra 40%</b><p>off Silver consectetur<br>adipiscing elit</p></div>
</div>

<div class="abs filters">
  <div class="filter" style="left:0;width:87px">Type<div class="select">Ring<svg viewBox="0 0 10 10"><path d="M2 3.5l3 3 3-3" stroke="#333" fill="none" stroke-width="1.3"/></svg></div></div>
  <div class="filter" style="left:111px;width:86px">Collection<div class="select">Select<svg viewBox="0 0 10 10"><path d="M2 3.5l3 3 3-3" stroke="#333" fill="none" stroke-width="1.3"/></svg></div></div>
  <div class="filter" style="left:221px;width:93px">Metal<div class="select">10% Rose Gold<svg viewBox="0 0 10 10"><path d="M2 3.5l3 3 3-3" stroke="#333" fill="none" stroke-width="1.3"/></svg></div></div>
  <div class="filter" style="left:340px;width:86px">Gemstone<div class="select">Amethyst<svg viewBox="0 0 10 10"><path d="M2 3.5l3 3 3-3" stroke="#333" fill="none" stroke-width="1.3"/></svg></div></div>
  <div class="filter" style="left:457px;width:85px">Price Range<div class="select">High to low<svg viewBox="0 0 10 10"><path d="M2 3.5l3 3 3-3" stroke="#333" fill="none" stroke-width="1.3"/></svg></div></div>
  <div class="filter" style="left:568px;width:109px">Sort By<div class="select">Our Favourite<svg viewBox="0 0 10 10"><path d="M2 3.5l3 3 3-3" stroke="#333" fill="none" stroke-width="1.3"/></svg></div></div>
</div>

<h2 class="abs section-title">Top Products</h2>
<div class="abs select sort-new">What's new<svg viewBox="0 0 10 10"><path d="M2 3.5l3 3 3-3" stroke="#333" fill="none" stroke-width="1.3"/></svg></div>
<div class="abs pager">
  <svg width="8" height="10" viewBox="0 0 8 10"><path d="M6 1L2 5l4 4" stroke="#333" fill="none" stroke-width="1.4"/></svg>
  <svg width="8" height="10" viewBox="0 0 8 10"><path d="M2 1l4 4-4 4" stroke="#333" fill="none" stroke-width="1.4"/></svg>
</div>

<article class="abs card" style="left:66px">
  <div class="card-photo"><div class="gem" role="img" aria-label="Sapphire ring with gold and diamond halo" style="background:radial-gradient(circle at 50% 30%,#2d4f86 0%,#c9b27a 30%,#e8e8e8 60%,#fff 80%)"></div>
    <div class="wish">Wishlist<svg viewBox="0 0 12 11"><path d="M6 10L1.5 5.5A2.6 2.6 0 016 2a2.6 2.6 0 014.5 3.5z" fill="none" stroke="#333" stroke-width="1"/></svg></div></div>
  <div class="card-body"><h3>Diamond Ring</h3><p class="sub">Silver plated</p><p class="desc">Neque porro quisquam est qui dolorem ipsum quia dolor sit amet,</p><p class="price">$29.00 CAD</p>
    <div class="actions"><span class="btn btn-cart">ADD TO CART</span><span class="btn btn-view">QUICK VIEW</span></div></div>
</article>
<article class="abs card" style="left:240px">
  <div class="card-photo"><div class="gem" role="img" aria-label="Emerald cut green stone ring in silver" style="background:radial-gradient(circle at 50% 35%,#1d8a3a 0%,#7dbb84 25%,#dcdcdc 50%,#fff 78%)"></div>
    <div class="wish">Wishlist<svg viewBox="0 0 12 11"><path d="M6 10L1.5 5.5A2.6 2.6 0 016 2a2.6 2.6 0 014.5 3.5z" fill="none" stroke="#333" stroke-width="1"/></svg></div></div>
  <div class="card-body"><h3>Diamond Ring</h3><p class="sub">Silver plated</p><p class="desc">Neque porro quisquam est qui dolorem ipsum quia dolor sit amet,</p><p class="price">$29.00 CAD</p>
    <div class="actions"><span class="btn btn-cart">ADD TO CART</span><span class="btn btn-view">QUICK VIEW</span></div></div>
</article>
<article class="abs card" style="left:415px">
  <div class="card-photo"><div class="gem" role="img" aria-label="Silver band set with emeralds and diamonds" style="top:50px;height:50px;background:radial-gradient(ellipse at 50% 50%,#1e7a45 0%,#9cc3a6 35%,#ececec 60%,#fff 80%)"></div>
    <div class="wish">Wishlist<svg viewBox="0 0 12 11"><path d="M6 10L1.5 5.5A2.6 2.6 0 016 2a2.6 2.6 0 014.5 3.5z" fill="#e94b4b"/></svg></div></div>
  <div class="card-body"><h3>Diamond Ring</h3><p class="sub">Silver plated</p><p class="desc">Neque porro quisquam est qui dolorem ipsum quia dolor sit amet,</p><p class="price">$29.00 CAD</p>
    <div class="actions"><span class="btn btn-cart">ADD TO CART</span><span class="btn btn-view">QUICK VIEW</span></div></div>
</article>
<article class="abs card" style="left:589px">
  <div class="card-photo"><div class="gem" role="img" aria-label="Diamond cluster ring with blue sapphire accents" style="background:radial-gradient(circle at 50% 40%,#f4f4f4 0%,#b9c1dc 25%,#2d3e9a 40%,#e6e6ee 60%,#fff 80%)"></div>
    <div class="wish">Wishlist<svg viewBox="0 0 12 11"><path d="M6 10L1.5 5.5A2.6 2.6 0 016 2a2.6 2.6 0 014.5 3.5z" fill="none" stroke="#333" stroke-width="1"/></svg></div></div>
  <div class="card-body"><h3>Diamond Ring</h3><p class="sub">Silver plated</p><p class="desc">Neque porro quisquam est qui dolorem ipsum quia dolor sit amet,</p><p class="price">$29.00 CAD</p>
    <div class="actions"><span class="btn btn-cart">ADD TO CART</span><span class="btn btn-view">QUICK VIEW</span></div></div>
</article>

<footer class="abs footer">
  <div class="fcol" style="left:67px"><h4>ABOUT US</h4><ul><li>Our Story</li><li>Wholesale inquiries</li></ul></div>
  <div class="fcol" style="left:213px"><h4>SHOPPING</h4><ul><li>Orders</li><li>Wishlist</li><li>Size Guide</li></ul></div>
  <div class="fcol" style="left:335px"><h4>CUSTOMER CARE</h4><ul><li>Returns</li><li>FAQs</li><li>Care &amp; Warranty</li><li>Contact Us</li></ul></div>
  <div class="fcol social" style="left:484px"><h4>SOCIAL LINKS</h4><ul style="margin-top:11px">
    <li><i style="background:#3b5998"></i>Circlepage</li>
    <li><i style="background:#c98a2a"></i>Snapframe</li>
    <li><i style="background:#e0252b"></i>Pinboardly</li></ul></div>
  <div class="fcol" style="left:605px"><h4>NEWSLETTER</h4>
    <div class="newsletter-form">
      <div class="nl-input"><svg width="10" height="8" viewBox="0 0 10 8"><rect x=".5" y=".5" width="9" height="7" fill="none" stroke="#333"/><path d="M.5.5L5 4.5 9.5.5" fill="none" stroke="#333"/></svg>Email address</div>
      <div class="nl-btn"><svg width="10" height="9" viewBox="0 0 10 9"><path d="M1 4.5h7M5 1l3.5 3.5L5 8" stroke="#fff" fill="none" stroke-width="1.8"/></svg></div>
    </div>
  </div>
</footer>

<div class="abs legal">
  <div class="pay"><span style="background:#f2f2f2"></span><span style="background:#e8e8e8"></span><span style="background:#f2f2f2"></span><span style="background:#4aa3df"></span></div>
  <p class="copy">© 2017 | www.companyname.com</p>
</div>

</body>
</html>
```